SnackOrbit!!! A Vending Machine Business Looking for an attractive website.

We are a vending machine business in Northern Michigan. We have changed our name and have rebranded our company. We would like an attractive website that shares who we are, what services we provide, the products we offer in our machines, along with a form businesses can fill out to see if they are a good fit for our company. I would like to have a Home Page, About SnackOrbit, Why Choose SnackOrbit?, Products & Services, Contact Us (With a Login Option), and a page with a questionnaire for thos interested in getting a FREE Vending Machine.

Target Market(s)

Businesses, Campgrounds, Schools, and many more in Northern Michigan

Industry/Entity Type

Vending Machines

Coding

Coded - Design and coding required

Number of Pages Required

5+ page

Requirements
Must have
• An inviting and enticing Home Page. I want to get my potential clients engaged in our website.
Nice to have
• Possibly background photos from Northern Michigan
Should not have
• A corporate feel. I do not want a boring website.

```html
<!DOCTYPE html>
<html lang="en">
<head>
<meta charset="utf-8">
<title>SnackOrbit – Vending Machines in Northern Michigan</title>
<link rel="stylesheet" href="https://fonts.googleapis.com/css2?family=Roboto:wght@400;500;700&family=Abril+Fatface&display=swap">
<style>
:root{
  --green:#2f5b29;
  --green-dark:#254a20;
  --navy:#1d2466;
  --navy-deep:#18205a;
  --ink:#222;
  --muted:#555;
  --footer:#2b2b2b;
  --white:#fff;
}
*{box-sizing:border-box;margin:0;padding:0}
html,body{width:1200px;height:4102px;overflow:hidden}
body{font-family:'Roboto',sans-serif;color:var(--ink);background:var(--white);position:relative}
.section{position:absolute;left:0;width:1200px}
.abs{position:absolute}
.display{font-family:'Abril Fatface',serif;color:var(--navy);text-shadow:2px 2px 0 var(--green),-1px -1px 0 #fff;letter-spacing:1px}
.btn{position:absolute;display:flex;align-items:center;justify-content:center;gap:8px;font-weight:700;font-size:13px;color:#fff;text-transform:uppercase;border-radius:3px}
.dot-icon{width:11px;height:11px;border-radius:50%;background:#fff;display:inline-block}
.arrow{position:absolute;font-size:30px;color:#222;font-weight:300}

/* header */
.topbar{top:0;height:64px}
.brand{position:absolute;left:111px;top:10px;display:flex;align-items:center;gap:8px}
.brand-mark{width:36px;height:36px;border-radius:50%;background:var(--navy)}
.brand-name{font-family:'Roboto',sans-serif;font-weight:700;font-size:30px;color:var(--navy)}
.social{position:absolute;display:flex;gap:8px}
.social span{width:32px;height:32px;border-radius:50%;border:1.5px solid #777;display:block}
.call-block{position:absolute;right:0;top:0;width:270px;height:105px;background:var(--navy-deep);clip-path:polygon(18px 0,100% 0,100% 100%,0 100%)}
.call-block .label{position:absolute;left:94px;top:31px;font-size:12px;color:#fff;font-weight:500}
.call-block .num{position:absolute;left:94px;top:52px;font-size:17px;color:#fff}
.phone-circle{position:absolute;width:40px;height:40px;border-radius:50%;border:2px solid #fff;display:flex;align-items:center;justify-content:center}
.nav{top:64px;height:41px;background:var(--green)}
.nav a{position:absolute;top:11px;font-size:15px;color:#fff;text-decoration:none}

/* hero */
.hero{top:105px;height:592px;background:linear-gradient(100deg,#5b5a55 0%,#8a8275 30%,#b9ad98 50%,#6e6a5f 75%,#4d4a44 100%)}
.hero h1{position:absolute;left:598px;top:170px;font-size:66px;font-weight:400}
.hero p{position:absolute;left:598px;top:262px;width:500px;font-size:16px;line-height:26px;color:#fff}

/* contact strip */
.touch{top:697px;height:220px;background:var(--green)}
.touch h2{position:absolute;width:100%;text-align:center;top:45px;font-size:36px;font-weight:400}
.field{position:absolute;top:118px;width:191px;height:43px;background:#fff;border-radius:2px;font-size:12px;color:#666;padding:15px 14px}

/* services */
.services{top:917px;height:706px}
.section-title{position:absolute;width:100%;text-align:center;font-size:40px;font-weight:400}
.service-card{position:absolute;width:308px;height:441px;background:#fff;border-radius:8px;box-shadow:0 3px 12px rgba(0,0,0,.22);text-align:center}
.service-card .photo{position:absolute;left:6px;top:6px;width:296px;height:213px;border-radius:6px}
.service-card h3{position:absolute;top:245px;width:100%;font-size:17px;font-weight:500}
.service-card p{position:absolute;top:278px;left:20px;right:20px;font-size:14px;line-height:22px;color:var(--muted)}
.outline-btn{position:absolute;left:76px;top:363px;width:155px;height:44px;border:2px solid var(--green);border-radius:4px;color:var(--green);font-weight:500;font-size:14px;display:flex;align-items:center;justify-content:center;gap:6px}
.outline-btn i{width:10px;height:10px;border-radius:50%;background:var(--green);display:inline-block}

/* who we are */
.about{top:1623px;height:599px;background:linear-gradient(180deg,#dfe2ec 0%,#eceef4 55%,#d8dce8 100%)}
.about h2{position:absolute;left:111px;top:135px;font-size:40px;font-weight:400}
.about p{position:absolute;left:111px;top:204px;width:455px;font-size:14.6px;line-height:26.6px;color:#333;text-align:justify}
.portrait{position:absolute;left:630px;top:70px;width:460px;height:460px;border-radius:50%;border:8px solid var(--navy);box-shadow:0 0 0 4px var(--green) inset;background:linear-gradient(135deg,#2a3f6b,#6b8ab0 45%,#c9a888 70%,#3a4a6a)}

/* products */
.products{top:2222px;height:558px}
.product{position:absolute;top:170px;width:234px;height:301px;border:1px solid #e2e2e2;background:#fff;text-align:center}
.product .photo{position:absolute;left:7px;top:8px;width:220px;height:199px;background:linear-gradient(180deg,#f6f6f6,#e8e8e8)}
.product .machine{position:absolute;left:77px;top:16px;width:66px;height:164px;border-radius:3px}
.product h3{position:absolute;top:228px;width:100%;font-size:17px;font-weight:500}
.product .price{position:absolute;left:32px;top:259px;font-size:21px;font-weight:500;color:#222}
.buy{position:absolute;left:117px;top:261px;width:86px;height:27px;background:var(--green-dark);color:#fff;font-size:10px;font-weight:700;display:flex;align-items:center;justify-content:center;border-radius:2px}

/* cta */
.cta{top:2780px;height:339px;background:linear-gradient(180deg,#1f2866,#1c2460);text-align:center}
.cta h2{position:absolute;width:100%;top:80px;font-size:40px;line-height:50px;font-weight:400;color:#fff;text-shadow:2px 2px 0 var(--green)}
.cta p{position:absolute;width:100%;top:200px;font-size:18px;line-height:29px;color:#fff;font-weight:500}

/* why choose */
.why{top:3119px;height:593px}
.badge{position:absolute;width:302px;height:302px;border-radius:50%;background:var(--navy);box-shadow:0 8px 12px rgba(0,0,0,.2)}
.badge .inner{position:absolute;left:16px;top:16px;right:16px;bottom:16px;border-radius:50%;background:var(--green);text-align:center;color:#fff}
.badge .icon{position:absolute;left:99px;top:-52px;width:104px;height:104px;border-radius:50%;background:var(--navy);display:flex;align-items:center;justify-content:center}
.badge h3{position:absolute;top:104px;width:100%;font-size:15px;font-weight:700}
.badge hr{position:absolute;top:140px;left:122px;width:26px;border:0;border-top:2px solid #fff}
.badge p{position:absolute;top:157px;left:30px;right:30px;font-size:13px;line-height:23.5px;text-align:justify;text-align-last:center}

/* footer */
.footer{top:3712px;height:390px;background:var(--footer);color:#fff}
.footer .brand-name{color:#fff;font-size:44px}
.fcol{position:absolute;top:89px}
.fcol h4{font-size:16px;font-weight:700;margin-bottom:18px}
.fcol a{display:block;font-size:13px;color:#fff;text-decoration:none;height:33px}
.contact-item{position:relative;padding-left:22px;font-size:13px;line-height:17px;margin-bottom:14px}
.contact-item b{font-size:11px;display:block}
.contact-item svg{position:absolute;left:0;top:2px}
.rule{position:absolute;left:111px;top:315px;width:976px;border-top:1px solid #555}
.copyright{position:absolute;left:434px;top:343px;font-size:14px}
.to-top{position:absolute;left:1131px;top:244px;width:36px;height:36px;border-radius:50%;background:var(--green);display:flex;align-items:center;justify-content:center}
</style>
</head>
<body>

<!-- Header -->
<header class="section topbar">
  <div class="brand"><span class="brand-mark"></span><span class="brand-name">SnackOrbit</span></div>
  <div class="social" style="left:541px;top:16px"><span></span><span></span><span></span><span></span></div>
  <div class="btn" style="left:721px;top:14px;width:204px;height:37px;background:var(--green);font-size:12px">Free Vending Machine <span class="dot-icon"></span></div>
</header>
<nav class="section nav">
  <a style="left:175px">Home</a>
  <a style="left:255px">About SnackOrbit</a>
  <a style="left:414px">Why Choose SnackOrbit?</a>
  <a style="left:625px">Products &amp; Services</a>
  <a style="left:800px">Contact Us</a>
</nav>
<div class="call-block">
  <div class="phone-circle" style="left:33px;top:33px">
    <svg width="20" height="20" viewBox="0 0 24 24" fill="#fff"><path d="M6.6 10.8a15 15 0 0 0 6.6 6.6l2.2-2.2c.3-.3.7-.4 1-.2 1.1.4 2.3.6 3.6.6.6 0 1 .4 1 1V20c0 .6-.4 1-1 1C10.6 21 3 13.4 3 4c0-.6.4-1 1-1h3.5c.6 0 1 .4 1 1 0 1.3.2 2.5.6 3.6.1.3 0 .7-.2 1z"/></svg>
  </div>
  <div class="label">Call Us Today</div>
  <div class="num">+1 555 010 2468</div>
</div>

<!-- Hero -->
<section class="section hero" role="img" aria-label="Photo of a smiling woman choosing a snack at a vending machine">
  <h1 class="display">SnackOrbit</h1>
  <p>Lorem ipsum dolor sit amet, consectetur adipiscing elit, sed dto eiusmod tempor incididunt ut labore et dolore magna aliqua.</p>
  <div class="btn" style="left:598px;top:344px;width:144px;height:46px;background:var(--navy);font-size:14px">Get Started</div>
</section>

<!-- Get in touch -->
<section class="section touch">
  <h2 class="display">Get In Touch</h2>
  <div class="field" style="left:108px">Name</div>
  <div class="field" style="left:307px">Phone Number</div>
  <div class="field" style="left:505px">Email</div>
  <div class="field" style="left:703px">No of Machines</div>
  <div class="btn" style="left:899px;top:118px;width:191px;height:43px;background:var(--navy);font-size:14px">Submit Now</div>
</section>

<!-- Services -->
<section class="section services">
  <h2 class="display section-title" style="top:68px">Our Services</h2>
  <div class="arrow" style="left:50px;top:370px">‹</div>
  <div class="arrow" style="left:1133px;top:370px">›</div>
  <div class="service-card" style="left:111px;top:159px">
    <div class="photo" role="img" aria-label="Woman buying snacks from a vending machine" style="background:linear-gradient(135deg,#6a5a4a,#c8b39a 50%,#8a2a2a)"></div>
    <h3>Snacks</h3>
    <p>Lorem ipsum dolor sit amet, consectetur adipiscing elit, sed do eiusmod tempor incididunt ut&nbsp; magna aliqua.</p>
    <div class="outline-btn">READ MORE <i></i></div>
  </div>
  <div class="service-card" style="left:446px;top:178px">
    <div class="photo" role="img" aria-label="Student holding a drink next to a vending machine" style="background:linear-gradient(135deg,#d8d8d8,#b04040 45%,#3a3a3a)"></div>
    <h3>Drinks</h3>
    <p>Lorem ipsum dolor sit amet, consectetur adipiscing elit, sed do eiusmod tempor incididunt ut&nbsp; magna aliqua.</p>
    <div class="outline-btn">READ MORE <i></i></div>
  </div>
  <div class="service-card" style="left:778px;top:159px">
    <div class="photo" role="img" aria-label="Fresh fruit in a locker-style vending machine" style="background:linear-gradient(135deg,#4a4a4a,#9a9a9a 45%,#c03030 60%,#5a5a5a)"></div>
    <h3>Healthy options</h3>
    <p>Lorem ipsum dolor sit amet, consectetur adipiscing elit, sed do eiusmod tempor incididunt ut&nbsp; magna aliqua.</p>
    <div class="outline-btn">READ MORE <i></i></div>
  </div>
</section>

<!-- Who we are -->
<section class="section about">
  <h2 class="display">Who We Are</h2>
  <p>Welcome to SnackOrbit, where snacking meets delight! We're not just about vending machines; we're your culinary companions, your flavor curators, and your secret stash of happiness. Mark and Elena, the dynamic duo behind SnackOrbit, have a passion for all things tasty. With backgrounds in sales and a penchant for personal connections, they've transformed the vending experience into an art form.</p>
  <div class="btn" style="left:111px;top:411px;width:148px;height:43px;background:var(--green-dark)">Read More <span class="dot-icon"></span></div>
  <div class="phone-circle" style="left:303px;top:411px;background:var(--navy);border:3px solid #fff;box-shadow:0 0 0 1px var(--navy)">
    <svg width="20" height="20" viewBox="0 0 24 24" fill="#fff"><path d="M6.6 10.8a15 15 0 0 0 6.6 6.6l2.2-2.2c.3-.3.7-.4 1-.2 1.1.4 2.3.6 3.6.6.6 0 1 .4 1 1V20c0 .6-.4 1-1 1C10.6 21 3 13.4 3 4c0-.6.4-1 1-1h3.5c.6 0 1 .4 1 1 0 1.3.2 2.5.6 3.6.1.3 0 .7-.2 1z"/></svg>
  </div>
  <div class="abs" style="left:358px;top:410px;font-size:12px;color:#333">Call Us Today</div>
  <div class="abs" style="left:358px;top:430px;font-size:20px;color:var(--navy);font-weight:500">+1 555 010 2468</div>
  <div class="portrait" role="img" aria-label="Woman selecting a drink at a glass-front vending machine"></div>
</section>

<!-- Products -->
<section class="section products">
  <h2 class="display section-title" style="top:82px">Our Products</h2>
  <div class="arrow" style="left:55px;top:300px">‹</div>
  <div class="arrow" style="left:1128px;top:300px">›</div>
  <div class="product" style="left:111px">
    <div class="photo" role="img" aria-label="Black snack vending machine"><div class="machine" style="background:linear-gradient(90deg,#222,#555,#222)"></div></div>
    <h3>Product Title</h3><div class="price">$25.00</div><div class="buy">BUY NOW</div>
  </div>
  <div class="product" style="left:360px">
    <div class="photo" role="img" aria-label="White snack vending machine"><div class="machine" style="background:linear-gradient(90deg,#ddd,#fff,#ccc)"></div></div>
    <h3>Product Title</h3><div class="price">$25.00</div><div class="buy">BUY NOW</div>
  </div>
  <div class="product" style="left:606px">
    <div class="photo" role="img" aria-label="Silver combo vending machine"><div class="machine" style="background:linear-gradient(90deg,#999,#e8e8e8,#999)"></div></div>
    <h3>Product Title</h3><div class="price">$25.00</div><div class="buy">BUY NOW</div>
  </div>
  <div class="product" style="left:855px">
    <div class="photo" role="img" aria-label="Black and orange drinks vending machine"><div class="machine" style="background:linear-gradient(90deg,#d07020,#333 15%,#444 85%,#d07020)"></div></div>
    <h3>Product Title</h3><div class="price">$25.00</div><div class="buy">BUY NOW</div>
  </div>
</section>

<!-- CTA -->
<section class="section cta">
  <h2 class="display">Ready To Experience The SnackOrbit<br>Difference?</h2>
  <p>Sign up now and let's connect. Taste the future of snacking firsthand! Contact us today<br>and explore how our vending magic can elevate your space</p>
</section>

<!-- Why choose -->
<section class="section why">
  <h2 class="display section-title" style="top:72px">Why Choose SnackOrbit?</h2>
  <div class="arrow" style="left:48px;top:318px">‹</div>
  <div class="arrow" style="left:1130px;top:318px">›</div>
  <div class="badge" style="left:112px;top:192px">
    <div class="inner"><h3>Local Love</h3><hr><p>We celebrate the heart of Michigan by partnering with local legends. Say hello to Pine Ridge Jerky and Lakeshore Crisp Chips</p></div>
    <div class="icon"><svg width="44" height="50" viewBox="0 0 44 50" fill="none" stroke="#fff" stroke-width="3"><rect x="6" y="3" width="32" height="44" rx="2"/><line x1="12" y1="12" x2="26" y2="12"/><line x1="12" y1="20" x2="26" y2="20"/><line x1="12" y1="28" x2="26" y2="28"/><line x1="32" y1="12" x2="32" y2="30"/></svg></div>
  </div>
  <div class="badge" style="left:449px;top:195px">
    <div class="inner"><h3>Unleash Your Cravings</h3><hr><p>SnackOrbit isn't bound by corporate ties. We're the rebels of the vending world. Craving a bag of crispy, kettle-cooked chips? Done.</p></div>
    <div class="icon"><svg width="44" height="50" viewBox="0 0 44 50" fill="none" stroke="#fff" stroke-width="3"><rect x="20" y="3" width="20" height="44" rx="2"/><line x1="25" y1="12" x2="35" y2="12"/><line x1="25" y1="22" x2="35" y2="22"/><circle cx="9" cy="12" r="4"/><line x1="9" y1="17" x2="9" y2="34"/><line x1="9" y1="34" x2="4" y2="46"/><line x1="9" y1="34" x2="14" y2="46"/></svg></div>
  </div>
  <div class="badge" style="left:786px;top:192px">
    <div class="inner"><h3>Quality Meets Convenience</h3><hr><p>Imagine this: You're mid-meeting, and your stomach growls. Fear not! SnackOrbit's machines offer top notch snacks and beverages.</p></div>
    <div class="icon"><svg width="50" height="50" viewBox="0 0 50 50" fill="none" stroke="#fff" stroke-width="3"><rect x="24" y="22" width="20" height="20" rx="3"/><path d="M28 22l4-14c3 0 4 2 3 6l-1 8"/><circle cx="14" cy="34" r="10"/><path d="M14 28l2 4 4 .5-3 3 .8 4-3.8-2-3.8 2 .8-4-3-3 4-.5z" fill="#fff" stroke="none"/></svg></div>
  </div>
</section>

<!-- Footer -->
<footer class="section footer">
  <div class="brand" style="left:111px;top:110px"><span class="brand-mark" style="background:#fff;width:40px;height:40px"></span><span class="brand-name">SnackOrbit</span></div>
  <div class="social" style="left:166px;top:208px;gap:6px"><span style="border-color:#fff"></span><span style="border-color:#fff"></span><span style="border-color:#fff"></span><span style="border-color:#fff"></span></div>
  <div class="fcol" style="left:434px"><h4>Quick Links</h4><a>Home</a><a>About SnackOrbit</a><a>Why Choose SnackOrbit?</a><a>Products &amp; Services</a><a>Contact Us</a></div>
  <div class="fcol" style="left:646px"><h4>About Company</h4><a>Terms of Use</a><a>Terms &amp; Condition</a><a>News</a><a>Contact Us</a><a>FAQ</a></div>
  <div class="fcol" style="left:871px;width:230px"><h4>Contact Us</h4>
    <div class="contact-item"><svg width="10" height="13" viewBox="0 0 10 13"><path d="M5 0a5 5 0 0 0-5 5c0 4 5 8 5 8s5-4 5-8a5 5 0 0 0-5-5z" fill="#4e8a44"/></svg><b>Location</b>418 Lorem ipsum dolor sit amet, consectetur adipiscing elit,</div>
    <div class="contact-item"><svg width="11" height="11" viewBox="0 0 24 24" fill="#4e8a44"><path d="M6.6 10.8a15 15 0 0 0 6.6 6.6l2.2-2.2c.3-.3.7-.4 1-.2 1.1.4 2.3.6 3.6.6.6 0 1 .4 1 1V20c0 .6-.4 1-1 1C10.6 21 3 13.4 3 4c0-.6.4-1 1-1h3.5c.6 0 1 .4 1 1 0 1.3.2 2.5.6 3.6.1.3 0 .7-.2 1z"/></svg><b>Phone</b>+1 555 010 2468</div>
    <div class="contact-item"><svg width="12" height="10" viewBox="0 0 12 10"><rect width="12" height="10" rx="1" fill="#4e8a44"/></svg><b>Email</b>info@snackorbit.com</div>
  </div>
  <div class="to-top"><svg width="14" height="10" viewBox="0 0 14 10" fill="none" stroke="#fff" stroke-width="2.5"><path d="M1 8l6-6 6 6"/></svg></div>
  <div class="rule"></div>
  <div class="copyright">2024 Copyright - SnackOrbit | All Rights Reserved</div>
</footer>

</body>
</html>
```